Pepo Darlo's Chimichurri Sauce

We need a label for a 10 ounce jar of a pesto type sauce using the argentine flag for color cues. the label would wrap around the jar. There would be room for how to use the sauce. About 20.5 cm length and 5 cm height. There would be a faded image of a man on a bycycle where the back story is told in 48 words with small signature and underneath a website there has to be room for the UPC code and also the ingrediant panel.

thhe back story over spanish looking boy with bike ideally near city scape but looking like it could be from 50's.

Young Darlo would bycycle from store to resataurant to grocer selling his Mother's jarred Chimichurri sauce. Each day the shop owners would say "Where is Pepodarlo?" The sauce handed down over generations is an Argentine national secret that makes every piece of meat, chicken, pasta, dip or eggs pop with excitement and bold taste. Warm Wishes From the Pampas....(signature) Pepo Darlo

The name of the product id Pepo Darlo's Chimichurri Warm Wishes From the Pampas
the label on back would be a box called Nutrition Facts. Serving Size 1 Tblsn (3g), Servings About 50 ;Amount Calories??/;Total Fat??/;Chol ??/Sodium???Total Carbs???Protein ????Vitamin A??Vitamin C;Calcium????????????????

Then Underneath that: Ingredients : Vegetable Oil,Vinegar,Parsley Garlic Chilli Fales,Pepper, Salt

The website: pepodarlos.example
Pepodarlos Foods LLC Maple Ridge, Ohio 44000

Some place else bold NON GMO NO PRESERVATIVES GLUEN FREE CHOLESTERAL FREE VEGAN PLEASE RECYCLE

Shoppers at high end grocery stores and farmer markets

Food Production

Colors
fbed22
ffffff
0292cd

• bright argentine colors and references
• The argentine flag is fun and colorful. Look at that. We want to make a back story of a young Pepodarlo bycycling through Buenes Aries in th e40's or 50's selling his mother's homemade sauce. This stuff tastes fantastic.

```html
<!DOCTYPE html>
<html lang="en">
<head>
<meta charset="utf-8">
<title>Pepo Darlo's Chimichurri – Jar Label</title>
<link rel="stylesheet" href="https://fonts.googleapis.com/css2?family=Archivo:wght@400;700;900&family=Cabin:wght@400;500&family=Kurale&family=Mrs+Saint+Delafield&display=swap">
<style>
  :root {
    --label-yellow: #f8d214;
    --page-white: #ffffff;
    --ribbon-blue: #6fa9df;
    --sauce-orange: #e36d1e;
    --heart-red: #d4572a;
    --ink-brown: #5a3d22;
    --leaf-green: #9cc25a;
    --panel-ink: #1e160c;
    --code-black: #231f20;
    --ring-orange: #f5a623;
  }
  * { box-sizing: border-box; margin: 0; padding: 0; }
  html, body {
    width: 1200px; height: 546px; overflow: hidden;
    background: var(--page-white);
  }
  .canvas { position: relative; width: 1200px; height: 546px; }
  .label {
    position: absolute; left: 21px; top: 125px;
    width: 1160px; height: 290px;
    background: var(--label-yellow);
  }
  .abs { position: absolute; }

  /* Back story panel */
  .story-art {
    left: 92px; top: 20px; width: 128px; height: 60px;
    background: radial-gradient(ellipse at 50% 55%, #c9a24a 0%, #e2bf3a 55%, var(--label-yellow) 80%);
    border-radius: 6px; opacity: .8;
  }
  .story-text {
    left: 50px; top: 87px; width: 220px;
    font-family: "Kurale", Georgia, serif;
    font-size: 10.3px; line-height: 12.3px;
    color: var(--ink-brown); text-align: justify;
  }
  .story-sign {
    right: 890px; top: 184px; white-space: nowrap; text-align: right;
    font-family: "Mrs Saint Delafield", cursive;
    font-size: 15px; line-height: 17px;
    color: var(--ink-brown);
  }
  .story-sign__name { display: block; }
  .barcode-box {
    left: 55px; top: 219px; width: 123px; height: 49px;
    background: var(--code-black);
    display: flex; align-items: center; justify-content: center;
    font-family: "Cabin", Arial, sans-serif; font-size: 23px;
    color: var(--page-white); letter-spacing: -.3px;
  }

  /* Front panel */
  .organic-mark {
    left: 434px; top: 20px; width: 150px; height: 64px;
    background: linear-gradient(160deg, rgba(111,169,223,.55), rgba(111,169,223,.25));
    border-radius: 30px 10px 30px 10px;
  }
  .scene { left: 491px; top: 54px; width: 156px; height: 156px; }
  .badge { top: 21px; width: 42px; height: 42px; border-radius: 50%; }
  .badge--gluten { left: 618px; background: #3a2c22; box-shadow: 0 0 0 3px #f0c330; }
  .badge--vegan { left: 667px; background: var(--leaf-green); }
  .title-ribbon { left: 420px; top: 181px; width: 305px; height: 32px; }
  .title-text {
    left: 420px; top: 181px; width: 305px; height: 32px;
    display: flex; align-items: center; justify-content: center;
    font-family: "Kurale", Georgia, serif;
    font-size: 20.5px; letter-spacing: .2px;
    color: var(--label-yellow); text-transform: uppercase;
  }
  .heart { left: 409px; top: 235px; }
  .heart-text {
    left: 409px; top: 246px; width: 46px; text-align: center;
    font-family: "Cabin", Arial, sans-serif;
    font-size: 5px; line-height: 6px; color: var(--label-yellow); font-weight: 500;
  }
  .wheat { left: 471px; top: 233px; width: 30px; height: 28px; border-radius: 6px; background: #c9d98a; }
  .pumpkin { left: 539px; top: 229px; width: 36px; height: 34px; border-radius: 50%; background: var(--sauce-orange); }
  .claim-label {
    top: 266px;
    font-family: "Kurale", Georgia, serif;
    font-size: 8px; color: var(--ink-brown); white-space: nowrap;
    -webkit-text-stroke: .25px var(--ink-brown);
  }
  .claim-label--gmo { left: 468px; }
  .claim-label--pres { left: 517px; }
  .net-weight {
    left: 649px; top: 244px;
    font-family: "Archivo", Arial, sans-serif; font-weight: 700;
    font-size: 19px; color: var(--sauce-orange); letter-spacing: -.5px;
  }

  /* Nutrition panel */
  .nutrition {
    left: 935px; top: 14px; width: 159px; height: 195px;
    background: var(--page-white); padding: 3px;
  }
  .nutrition__box {
    width: 100%; height: 100%;
    border: 2px solid var(--panel-ink);
    padding: 2px 5px;
    font-family: "Archivo", Arial, sans-serif;
    color: var(--panel-ink);
    overflow: hidden;
  }
  .nutrition__title { font-weight: 900; font-size: 16px; line-height: 16px; letter-spacing: -.2px; }
  .nutrition__serving { font-size: 5.2px; font-weight: 700; line-height: 5.5px; }
  .nutrition__serving--small { font-size: 4.4px; }
  .nutrition__bar { background: var(--panel-ink); height: 5px; margin: 1.5px 0; }
  .nutrition__rule { border-top: 2px solid var(--panel-ink); margin: 0; }
  .nutrition__row {
    display: flex; justify-content: space-between;
    font-size: 4.6px; line-height: 5.8px; font-weight: 700;
    border-bottom: .5px solid #8a8070;
  }
  .nutrition__row--sub { padding-left: 5px; }
  .nutrition__row--plain { border-bottom: 0; }
  .nutrition__row--right { justify-content: flex-end; }
  .nutrition__row--small { font-size: 4.2px; }
  .nutrition__note { font-size: 4.3px; line-height: 4.8px; font-weight: 700; margin-top: 1px; }

  /* Back panel */
  .recycle { left: 847px; top: 236px; width: 30px; height: 30px; }
  .recycle-label {
    left: 827px; top: 266px; width: 70px; text-align: center; white-space: nowrap;
    font-family: "Kurale", Georgia, serif; font-size: 8px; color: var(--ink-brown);
    -webkit-text-stroke: .25px var(--ink-brown);
  }
  .info {
    left: 905px; top: 220px; width: 222px;
    font-family: "Cabin", Arial, sans-serif; font-size: 10px; line-height: 12.4px;
    color: var(--ink-brown);
  }
  .info__ingredients { margin-bottom: 10px; }
</style>
</head>
<body>
<div class="canvas">
  <section class="label">

    <!-- Back story -->
    <div class="abs story-art" role="img" aria-label="Vintage sketch of a young man riding a bicycle"></div>
    <p class="abs story-text">Young Darlo would bycycle from store to resataurant to grocer selling his Mother's jarred Chimichurri sauce. Each day the shop owners would say "Where is Pepodarlo?" The sauce handed down over generations is an Argentine national secret that makes every piece of meat, chicken, pasta, dip or eggs pop with excitement and bold taste.</p>
    <p class="abs story-sign">Warm Wishes From the Pampas<span class="story-sign__name">Pepo Darlo</span></p>
    <div class="abs barcode-box">BAR CODE</div>

    <!-- Front panel -->
    <div class="abs organic-mark" role="img" aria-label="Organic, All Natural ribbon lettering with laurel sprigs"></div>
    <div class="abs badge badge--gluten" role="img" aria-label="Gluten free seal"></div>
    <div class="abs badge badge--vegan" role="img" aria-label="Vegan seal"></div>

    <svg class="abs scene" viewBox="0 0 156 156" role="img" aria-label="Farm scene with barn, sun, hills and crop fields">
      <defs>
        <radialGradient id="scene-fill" cx="50%" cy="40%" r="60%">
          <stop offset="0%" stop-color="#fdf8e6"/>
          <stop offset="55%" stop-color="#f6e4a0"/>
          <stop offset="100%" stop-color="#f3c24d"/>
        </radialGradient>
      </defs>
      <circle cx="78" cy="78" r="75" fill="url(#scene-fill)" stroke="var(--ring-orange)" stroke-width="4"/>
    </svg>

    <svg class="abs title-ribbon" viewBox="0 0 305 32" aria-hidden="true">
      <polygon points="0,0 305,0 293,16 305,32 0,32 12,16" fill="var(--ribbon-blue)"/>
    </svg>
    <div class="abs title-text">Pepo Darlo's Chimichurri</div>

    <svg class="abs heart" width="46" height="39" viewBox="0 0 44 38" aria-hidden="true">
      <path d="M22 37 C8 26 0 19 0 10 C0 4 5 0 11 0 C16 0 20 3 22 7 C24 3 28 0 33 0 C39 0 44 4 44 10 C44 19 36 26 22 37Z" fill="var(--heart-red)"/>
    </svg>
    <div class="abs heart-text">NO<br>CHOLESTEROL</div>

    <div class="abs wheat" role="img" aria-label="Wheat stalks icon"></div>
    <div class="abs claim-label claim-label--gmo">NON GMO</div>

    <div class="abs pumpkin" role="img" aria-label="Pumpkin icon"></div>
    <div class="abs claim-label claim-label--pres">NO PRESERVATIVES</div>

    <div class="abs net-weight">10oz</div>

    <!-- Nutrition panel -->
    <div class="abs nutrition">
      <div class="nutrition__box">
        <div class="nutrition__title">Nutrition Facts</div>
        <div class="nutrition__serving">Serving Size &nbsp;&nbsp;larger than life</div>
        <div class="nutrition__serving nutrition__serving--small">Servings Per Container 1</div>
        <div class="nutrition__bar"></div>
        <div class="nutrition__row nutrition__row--plain nutrition__row--small">Amount Per Serving</div>
        <div class="nutrition__row"><span>Calories Unlimited</span><span>Calories from Love 100%</span></div>
        <div class="nutrition__rule"></div>
        <div class="nutrition__row nutrition__row--right"><span>% Daily Value*</span></div>
        <div class="nutrition__rule"></div>
        <div class="nutrition__row"><span>Total &nbsp;Satisfaction</span><span>100%</span></div>
        <div class="nutrition__row nutrition__row--sub"><span>Passion</span><span>100%</span></div>
        <div class="nutrition__row nutrition__row--sub"><span>Happiness</span><span>100%</span></div>
        <div class="nutrition__row nutrition__row--sub"><span>Creativity</span><span>100%</span></div>
        <div class="nutrition__row nutrition__row--sub"><span>Wonder</span><span>100%</span></div>
        <div class="nutrition__row nutrition__row--sub"><span>Self-Esteem</span><span>100%</span></div>
        <div class="nutrition__row nutrition__row--sub"><span>Integrity</span><span>100%</span></div>
        <div class="nutrition__row nutrition__row--sub"><span>Empathy</span><span>100%</span></div>
        <div class="nutrition__row nutrition__row--sub"><span>Patience</span><span>100%</span></div>
        <div class="nutrition__row nutrition__row--sub"><span>Relationships</span><span>100%</span></div>
        <div class="nutrition__row nutrition__row--sub"><span>Rest</span><span>100%</span></div>
        <div class="nutrition__row nutrition__row--sub"><span>Fitness</span><span>100%</span></div>
        <div class="nutrition__row nutrition__row--sub nutrition__row--plain"><span>Taking Action</span><span>100%</span></div>
        <div class="nutrition__bar"></div>
        <p class="nutrition__note">* Percent daily values are based on fully accepting the now and living in the present. Actual daily values may be higher or lower depending on lifestyle, focus, personal development, stress levels, and overall sense of purpose.</p>
      </div>
    </div>

    <!-- Back panel -->
    <svg class="abs recycle" viewBox="0 0 26 26" aria-hidden="true">
      <polygon points="13,2 24,22 2,22" fill="none" stroke="var(--leaf-green)" stroke-width="4" stroke-linejoin="round"/>
    </svg>
    <div class="abs recycle-label">PLEASE RECYCLE</div>

    <div class="abs info">
      <p class="info__ingredients">Ingredients &nbsp;: &nbsp;Vegetable Oil,Vinegar,Parsley Garlic Chilli Fales,Pepper, Salt</p>
      <p>The website: pepodarlos.example</p>
      <p>Pepodarlos Foods LLC Maple Ridge, Ohio 44000</p>
    </div>

  </section>
</div>
</body>
</html>
```